Dalvick's Business Card

I need some designs for a new business card including the new logo attached. An old example of our business card is also attached to show all the data that should be included on the new design.
**I added some more examples someone had mocked up**

Contact Information for Business Card

Should include all info on other examples uploaded.

```html
<!DOCTYPE html>
<html lang="en">
<head>
<meta charset="utf-8">
<title>Dalvick's Business Card</title>
<link href="https://fonts.googleapis.com/css2?family=Montserrat:wght@400;500;600;800&display=swap" rel="stylesheet">
<style>
  :root {
    --brand-blue: #0b67b1;
    --brand-blue-dark: #07539a;
    --brand-red: #de1f26;
    --brand-red-dark: #cc161d;
    --paper: #f6f6f6;
    --backdrop: #e6e6e6;
    --white: #ffffff;
  }
  * { margin: 0; padding: 0; box-sizing: border-box; }
  html, body { width: 1200px; height: 1200px; overflow: hidden; }
  body {
    background: var(--backdrop);
    font-family: "Montserrat", sans-serif;
    position: relative;
  }
  .card {
    position: absolute;
    left: 234px;
    width: 730px;
    height: 417px;
    overflow: hidden;
  }
  /* Front */
  .card-front { top: 160px; background: var(--paper); }
  .brand-mark {
    position: absolute;
    left: 60px; top: 72px;
    width: 62px; height: 62px;
    border-radius: 50%;
    background: var(--brand-red);
  }
  .brand-name {
    position: absolute;
    left: 137px; top: 72px;
    font-weight: 600;
    font-size: 46px;
    letter-spacing: 0.5px;
    color: var(--brand-blue);
    line-height: 1;
  }
  .brand-tagline {
    position: absolute;
    left: 138px; top: 117px;
    font-weight: 600;
    font-size: 12.2px;
    color: var(--brand-red);
    white-space: nowrap;
  }
  .person-name {
    position: absolute;
    left: 137px; top: 228px;
    font-weight: 800;
    font-size: 30.5px;
    color: var(--brand-red);
  }
  .contact-line {
    position: absolute;
    left: 135px;
    display: flex; align-items: center; gap: 8px;
    font-size: 23px;
    font-weight: 400;
    color: var(--brand-blue);
  }
  .contact-phone { top: 268px; }
  .contact-email { top: 299px; }
  .contact-line svg { width: 18px; height: 18px; flex: none; }
  .house-art {
    position: absolute;
    left: 550px; top: 311px;
    width: 129px; height: 60px;
    background: linear-gradient(to bottom, var(--brand-blue), var(--brand-red));
  }
  .front-band {
    position: absolute; left: 0; right: 0; bottom: 0; height: 45px;
  }
  .band-licensed {
    position: absolute; left: 0; top: 0; bottom: 0; width: 348px;
    background: var(--brand-blue);
    clip-path: polygon(0 0, 100% 0, 88% 100%, 0 100%);
  }
  .band-family {
    position: absolute; left: 316px; right: 0; top: 0; bottom: 0;
    background: var(--brand-red);
    clip-path: polygon(44px 0, 100% 0, 100% 100%, 0 100%);
  }
  .band-text {
    position: absolute; top: 11px;
    color: var(--white);
    font-size: 19.6px;
    font-weight: 400;
    letter-spacing: 0.3px;
    white-space: nowrap;
  }
  .band-text-left { left: 47px; }
  .band-text-right { left: 388px; }

  /* Back */
  .card-back {
    top: 631px;
    background: linear-gradient(160deg, var(--brand-blue-dark), var(--brand-blue) 70%, #0c72b8);
  }
  .back-top {
    position: absolute; left: 0; right: 0; top: 0; height: 66px;
    background: var(--brand-red);
    display: flex; align-items: center; justify-content: center;
    color: var(--white);
    font-size: 24px; font-weight: 400; letter-spacing: 0.2px;
  }
  .notch {
    position: absolute; left: 342px; width: 46px; height: 23px;
    background: var(--brand-red);
  }
  .notch-down { top: 65px; clip-path: polygon(0 0, 100% 0, 50% 100%); }
  .notch-up { top: 329px; clip-path: polygon(50% 0, 100% 100%, 0 100%); }
  .back-bottom {
    position: absolute; left: 0; right: 0; top: 351px; bottom: 0;
    background: var(--brand-red-dark);
    display: flex; align-items: center; justify-content: center;
    color: var(--white);
    font-size: 17.4px; font-weight: 400; letter-spacing: 0.3px;
    white-space: nowrap;
  }
  .back-mark {
    position: absolute; left: 150px; top: 172px;
    width: 78px; height: 78px; border-radius: 50%;
    background: var(--white);
  }
  .back-name {
    position: absolute; left: 254px; top: 172px;
    font-weight: 600; font-size: 62px; line-height: 1;
    color: var(--white);
    letter-spacing: 0.5px;
  }
  .back-tagline {
    position: absolute; left: 255px; top: 238px;
    font-weight: 600; font-size: 16.4px;
    color: var(--white);
    white-space: nowrap;
  }
</style>
</head>
<body>
  <section class="card card-front">
    <div class="brand-mark"></div>
    <div class="brand-name">DALVICK'S</div>
    <div class="brand-tagline">AIR CONDITIONING &amp; HEATING SERVICE</div>

    <div class="person-name">MARK DALVICK</div>
    <div class="contact-line contact-phone">
      <svg viewBox="0 0 24 24" aria-hidden="true"><path fill="#de1f26" d="M6.6 10.8a15.5 15.5 0 0 0 6.6 6.6l2.2-2.2c.3-.3.7-.4 1-.2 1.1.4 2.3.6 3.6.6.6 0 1 .4 1 1V20c0 .6-.4 1-1 1A17 17 0 0 1 3 4c0-.6.4-1 1-1h3.5c.6 0 1 .4 1 1 0 1.3.2 2.5.6 3.6.1.3 0 .7-.2 1z"/></svg>
      <span>555.014.2290</span>
    </div>
    <div class="contact-line contact-email">
      <svg viewBox="0 0 24 24" aria-hidden="true"><rect x="2" y="5" width="20" height="14" rx="1.5" fill="#de1f26"/><path d="M2.5 6l9.5 7 9.5-7" fill="none" stroke="#f6f6f6" stroke-width="1.6"/></svg>
      <span>hvacdalvick@mail.com</span>
    </div>

    <div class="house-art" role="img" aria-label="Illustration of a house roof with chimney and window"></div>

    <div class="front-band">
      <div class="band-licensed"></div>
      <div class="band-family"></div>
      <span class="band-text band-text-left">LICENSED &amp; INSURED</span>
      <span class="band-text band-text-right">FAMILY OWNED &amp; OPERATED</span>
    </div>
  </section>

  <section class="card card-back">
    <div class="back-top">SERVES MAPLEWOOD, IA &amp; SURROUNDING AREAS</div>
    <div class="notch notch-down"></div>

    <div class="back-mark"></div>
    <div class="back-name">DALVICK'S</div>
    <div class="back-tagline">AIR CONDITIONING &amp; HEATING SERVICE</div>

    <div class="notch notch-up"></div>
    <div class="back-bottom">CALL TODAY FOR ALL YOUR HVAC, REFRIGERATION &amp; PLUMBING NEEDS</div>
  </section>
</body>
</html>
```